Corvane Holdings , new business card design

investment firm with corporate clients . need double sided business card , vertical and horizontal options ,logo must be clear. prefer pantone colors only and sharp design. website also www.corvane.ae

Khalid Bin Tarrafi
Managing Director
Tel. +971 4 387 2940
Mobile +971 50 518 2403
khalid@corvane.ae
Q-Span Plaza, officw 18-B07, Warqa Gardens, Dubai

Contact Information for Business Card

Khalid Bin Tarrafi
Managing Director

Font styles to use
Serif

Colors

Designer to choose colors to be used in the design.

```html
<!DOCTYPE html>
<html lang="en">
<head>
<meta charset="utf-8">
<title>Corvane Holdings — Business Card</title>
<link rel="stylesheet" href="https://fonts.googleapis.com/css2?family=Roboto:wght@300;400&family=Roboto+Condensed:wght@400;500&display=swap">
<style>
  :root {
    --backdrop: #262626;
    --card-paper: #f1f1f1;
    --brand-blue: #52799e;
    --ink: #1c1c1c;
    --ink-soft: #4a4a4a;
    --white: #ffffff;
  }
  * { margin: 0; padding: 0; box-sizing: border-box; }
  html, body {
    width: 1200px; height: 960px; overflow: hidden;
    background: var(--backdrop);
    font-family: "Roboto", Arial, sans-serif;
  }
  .canvas { position: relative; width: 1200px; height: 960px; }
  .card {
    position: absolute; width: 600px; height: 343px;
    background: var(--card-paper);
    box-shadow: 0 3px 8px rgba(0,0,0,0.45);
    overflow: hidden;
  }
  .card--front { left: 152px; top: 125px; }
  .card--back { left: 452px; top: 500px; }

  .front-band {
    position: absolute; left: 0; top: 0; width: 100%; height: 123px;
    background: var(--brand-blue);
  }
  .front-band__name {
    position: absolute; left: 36px; top: 44px;
    font-family: "Roboto", Arial, sans-serif; font-weight: 300;
    font-size: 40px; letter-spacing: 20px; color: var(--white);
    line-height: 1;
  }

  .address {
    position: absolute; left: 37px; top: 215px;
    font-size: 14px; line-height: 19px; color: var(--ink-soft);
  }
  .address__line { display: flex; align-items: center; gap: 8px; }
  .icon { width: 12px; height: 13px; flex: none; fill: var(--brand-blue); }

  .person { position: absolute; left: 348px; top: 168px; }
  .person__name {
    font-family: "Roboto Condensed", "Arial Narrow", sans-serif; font-weight: 500;
    font-size: 20px; color: var(--brand-blue); text-transform: uppercase; line-height: 24px;
  }
  .person__title {
    font-size: 14.5px; color: var(--ink); text-transform: uppercase; line-height: 18px;
  }
  .person__rule {
    width: 37px; height: 3px; background: var(--brand-blue); margin: 8px 0 10px;
  }
  .contact-list { list-style: none; font-size: 14px; line-height: 19px; color: var(--ink-soft); }
  .contact-list li { display: flex; align-items: center; gap: 7px; }

  .back-mark {
    position: absolute; left: 0; top: 140px; width: 100%; text-align: center;
    font-family: "Roboto", Arial, sans-serif; font-weight: 300;
    font-size: 30px; letter-spacing: 12px; color: var(--ink);
    padding-left: 12px; line-height: 1;
  }
  .back-web {
    position: absolute; left: 0; top: 290px; width: 100%; text-align: center;
    font-size: 14px; letter-spacing: 9.5px; color: var(--ink-soft);
    padding-left: 9px;
  }
</style>
</head>
<body>
<main class="canvas">

  <section class="card card--front" aria-label="Business card front">
    <div class="front-band">
      <p class="front-band__name">CORVANE</p>
    </div>

    <address class="address" style="font-style: normal;">
      <div class="address__line">
        <svg class="icon" viewBox="0 0 12 16" aria-hidden="true"><path d="M6 0a6 6 0 0 0-6 6c0 4.5 6 10 6 10s6-5.5 6-10a6 6 0 0 0-6-6zm0 8.5A2.5 2.5 0 1 1 6 3.5a2.5 2.5 0 0 1 0 5z"/></svg>
        <span>Q-Span Plaza, officw 18-B07</span>
      </div>
      <div>Warqa Gardens, Dubai</div>
    </address>

    <div class="person">
      <h1 class="person__name">Khalid Bin Tarrafi</h1>
      <p class="person__title">Managing Director</p>
      <div class="person__rule"></div>
      <ul class="contact-list">
        <li>
          <svg class="icon" viewBox="0 0 16 16" aria-hidden="true"><path d="M3.6 0.8l2.3 2.8c.4.5.3 1.1-.1 1.5L4.6 6.2a10 10 0 0 0 5.2 5.2l1.1-1.2c.4-.4 1-.5 1.5-.1l2.8 2.3c.5.4.5 1.1.1 1.5l-1.4 1.4C12.4 16.8 0 8 .7 2.6L2.1 1.2c.4-.4 1.1-.4 1.5-.4z"/></svg>
          <span>+971 4 387 2940</span>
        </li>
        <li>
          <svg class="icon" viewBox="0 0 12 16" aria-hidden="true"><path d="M2 0h8a2 2 0 0 1 2 2v12a2 2 0 0 1-2 2H2a2 2 0 0 1-2-2V2a2 2 0 0 1 2-2zm0 2v10h8V2zm4 11a1 1 0 1 0 0 2 1 1 0 0 0 0-2z"/></svg>
          <span>+971 50 518 2403</span>
        </li>
        <li>
          <svg class="icon" viewBox="0 0 16 12" aria-hidden="true"><path d="M0 1v10h16V1L8 7z"/><path d="M0.5 0h15L8 5.5z"/></svg>
          <span>khalid@corvane.ae</span>
        </li>
        <li>
          <svg class="icon" viewBox="0 0 16 16" aria-hidden="true"><path d="M8 0a8 8 0 1 0 0 16A8 8 0 0 0 8 0zm0 1.5c1 0 2 2 2.3 5H5.7C6 3.5 7 1.5 8 1.5zM5.7 8h4.6c-.3 3-1.3 5-2.3 5s-2-2-2.3-5z"/></svg>
          <span>www.corvane.ae</span>
        </li>
      </ul>
    </div>
  </section>

  <section class="card card--back" aria-label="Business card back">
    <p class="back-mark">CORVANE HOLDINGS</p>
    <p class="back-web">www.corvane.ae</p>
  </section>

</main>
</body>
</html>
```